Kelvaro.ch is looking for business card letterhead and envelope C5 with WOW effect

We need a strong business card for our company Kelvaro.ch, logo is available. You want a black or dark background on which the logo Stark r% 26 # 252; appears. Letterhead and envelope in C5 format should be in a similar design, but does not have to be We need a strong business card for our company Kelvaro.ch, logo is available. A black or dark background is desired, on which the logo Stark comes across. The letterhead and the envelope in C5 format should have a similar design.

Target Market(s)

Private customers as well as entrepreneurs

Contact Information for Business Card

E-mail: info@kelvaro-example.ch
Web.www.Kelvaro-example.ch
Tel: +41 ( 0 ) 79 482 6037
Adresse:
Lindenweg 14
9406 Tarnbach

Hier kann man Icons verwenden für Email,Tel und Adressse

Font styles to use
Other font styles liked:
• Dubai,bold

Colors

Designer to choose colors to be used in the design.

Requirements
Must have
• WOW effect
Nice to have
• R% 26 # 252; back business card with our service listings. - VEHICLE LABELING - SHOP WINDOW LABELING - STICKERS AND MUCH MORE ... in red color

```html
<!DOCTYPE html>
<html lang="en">
<head>
<meta charset="utf-8">
<title>Kelvaro.ch Business Card</title>
<link href="https://fonts.googleapis.com/css2?family=Roboto:wght@400;500;700&display=swap" rel="stylesheet">
<style>
  :root {
    --backdrop: #2a2a2b;
    --card-dark: #1d1d1f;
    --brand-yellow: #f8c514;
    --pattern-yellow: #f3be12;
    --ink-light: #f2f2f2;
    --ink-dark: #1a1a1a;
    --rule: #6a6a6a;
  }
  * { box-sizing: border-box; margin: 0; padding: 0; }
  html, body { width: 1200px; height: 1108px; overflow: hidden; }
  body {
    background: var(--backdrop);
    font-family: "Roboto", Arial, sans-serif;
    display: flex;
    align-items: center;
    justify-content: center;
    gap: 60px;
  }
  .card {
    width: 420px;
    height: 680px;
    border-radius: 24px;
    position: relative;
    overflow: hidden;
    box-shadow: 0 18px 40px rgba(0,0,0,0.45);
  }
  /* front */
  .card--front { background: var(--card-dark); color: var(--ink-light); }
  .brand {
    position: absolute;
    left: 0; right: 0;
    top: 150px;
    display: flex;
    align-items: center;
    justify-content: center;
    gap: 18px;
  }
  .brand__mark { width: 56px; height: 56px; }
  .brand__name {
    font-weight: 700;
    font-size: 40px;
    letter-spacing: 1px;
    text-transform: uppercase;
  }
  .card--front .brand__mark { background: var(--brand-yellow); }
  .card--front .brand__name { color: var(--ink-light); }

  .contact {
    position: absolute;
    left: 40px; right: 40px;
    top: 390px;
    text-align: center;
  }
  .contact__icons {
    display: flex;
    align-items: center;
    gap: 8px;
    justify-content: center;
  }
  .contact__icons .rule { flex: 1; height: 1px; background: var(--rule); }
  .icon-tile {
    width: 34px; height: 34px;
    background: var(--brand-yellow);
    border-radius: 4px;
    display: flex; align-items: center; justify-content: center;
  }
  .icon-tile svg { width: 22px; height: 22px; }
  .contact__lines { margin-top: 14px; font-size: 24px; line-height: 31px; }
  .contact__web { color: var(--brand-yellow); }
  .contact__divider { height: 1px; background: var(--rule); margin: 18px 0 18px; }
  .address { font-size: 26px; line-height: 33px; }

  /* back */
  .card--back { background: var(--brand-yellow); color: var(--ink-dark); }
  .pattern-field {
    position: absolute; inset: 0;
    background: linear-gradient(160deg, var(--brand-yellow), var(--pattern-yellow));
  }
  .card--back .brand { top: 330px; }
  .card--back .brand__mark { background: var(--ink-dark); }
  .card--back .brand__name { color: var(--ink-dark); }
  .services {
    position: absolute;
    left: 0; right: 0;
    bottom: 70px;
    text-align: center;
    font-size: 22px;
    line-height: 30px;
    text-transform: uppercase;
  }
</style>
</head>
<body>
  <section class="card card--front">
    <div class="brand">
      <span class="brand__mark"></span>
      <span class="brand__name">Kelvaro.ch</span>
    </div>
    <div class="contact">
      <div class="contact__icons">
        <span class="rule"></span>
        <span class="icon-tile">
          <svg viewBox="0 0 24 24" aria-label="Phone"><path fill="#1d1d1f" d="M6.6 10.8a15.1 15.1 0 0 0 6.6 6.6l2.2-2.2a1 1 0 0 1 1-.25 11.4 11.4 0 0 0 3.6.57 1 1 0 0 1 1 1V20a1 1 0 0 1-1 1A17 17 0 0 1 3 4a1 1 0 0 1 1-1h3.5a1 1 0 0 1 1 1c0 1.25.2 2.45.57 3.57a1 1 0 0 1-.25 1z"/></svg>
        </span>
        <span class="icon-tile">
          <svg viewBox="0 0 24 24" aria-label="Email"><rect x="3" y="6" width="18" height="12" fill="none" stroke="#1d1d1f" stroke-width="2"/><path d="M3 6l9 7 9-7" fill="none" stroke="#1d1d1f" stroke-width="2"/></svg>
        </span>
        <span class="icon-tile">
          <svg viewBox="0 0 24 24" aria-label="Website"><circle cx="12" cy="12" r="8.5" fill="none" stroke="#1d1d1f" stroke-width="2"/><path d="M3.5 12h17M12 3.5c3 3 3 14 0 17M12 3.5c-3 3-3 14 0 17" fill="none" stroke="#1d1d1f" stroke-width="1.6"/></svg>
        </span>
        <span class="rule"></span>
      </div>
      <div class="contact__lines">
        <div>+41 ( 0 ) 79 482 6037</div>
        <div>info@kelvaro-example.ch</div>
        <div class="contact__web">www.Kelvaro-example.ch</div>
      </div>
      <div class="contact__divider"></div>
      <div class="address">
        <div>Lindenweg 14</div>
        <div>9406 Tarnbach</div>
      </div>
    </div>
  </section>

  <section class="card card--back">
    <div class="pattern-field" role="img" aria-label="Subtle tone-on-tone hexagon pattern across the yellow card"></div>
    <div class="brand">
      <span class="brand__mark"></span>
      <span class="brand__name">Kelvaro.ch</span>
    </div>
    <div class="services">
      <div>Vehicle labeling</div>
      <div>Shop window labeling</div>
      <div>Stickers and much more ...</div>
    </div>
  </section>
</body>
</html>
```